Business Card for my New Brokerage

Looking to get a business card design for my new Real Estate Brokerage.
I want it with Picture, Phone Number, Email, Website, Office Address
Name and Designation. Please add logo too.

Target Market(s)

Real Estate Investors or Home Buyers

Industry/Entity Type

Real Estate

Contact Information for Business Card

Name, Email, Phone Number, website, email, office address

Colors
EB3D1F
EC4F4E
F09395
F8D3D4
FCEDEE

Requirements
Must have
• Minimalistic, Clean, Modern, Photo
Nice to have
• White and Red Colors

```html
<!DOCTYPE html>
<html lang="en">
<head>
<meta charset="utf-8">
<title>Ember Realty Inc – Business Card</title>
<link href="https://fonts.googleapis.com/css2?family=Montserrat:wght@400;500;700;800&display=swap" rel="stylesheet">
<style>
  :root {
    --brand-red: #dd0000;
    --gold: #d4b25a;
    --ink: #4a4a4a;
    --paper: #ffffff;
    --backdrop: #2a2a2a;
    --suit-navy: #1c2438;
    --shirt-blue: #bcd3ee;
  }
  * { box-sizing: border-box; margin: 0; padding: 0; }
  html, body {
    width: 1200px; height: 900px; overflow: hidden;
    background: var(--backdrop);
    font-family: "Montserrat", sans-serif;
  }
  .stage {
    position: relative; width: 1200px; height: 900px;
    display: flex; flex-direction: column; align-items: center; justify-content: center; gap: 40px;
  }
  .card {
    position: relative; width: 700px; height: 400px; overflow: hidden;
    box-shadow: 0 12px 30px rgba(0,0,0,.45);
  }
  /* Front */
  .card--front { background: var(--paper); }
  .card__swoosh { position: absolute; inset: 0; width: 100%; height: 100%; }
  .company-name {
    position: absolute; left: 60px; top: 110px;
    color: var(--brand-red); font-weight: 700;
    font-size: 36px; line-height: 1.15; letter-spacing: 0;
  }
  .divider {
    position: absolute; left: 345px; top: 92px; width: 1.5px; height: 178px;
    background: var(--brand-red);
  }
  .contact {
    position: absolute; left: 368px; top: 92px; color: var(--ink);
    font-size: 15px; line-height: 1.42; font-weight: 500;
  }
  .contact__name { color: var(--brand-red); font-weight: 800; font-size: 24px; letter-spacing: .5px; line-height: 1.1; }
  .contact__role { font-size: 15px; margin-bottom: 8px; }
  .contact__list { list-style: none; }
  .contact__list li { display: flex; align-items: center; gap: 7px; }
  .contact__list svg { width: 12px; height: 12px; flex: none; }
  /* Back */
  .card--back { background: var(--brand-red); }
  .portrait {
    position: absolute; left: 40px; bottom: 0; width: 280px; height: 360px;
    border-radius: 140px 140px 0 0;
    background: linear-gradient(180deg, #5a4a44 0%, #3a3d4a 35%, var(--suit-navy) 60%, #2c3650 100%);
  }
  .company-name--light { color: var(--paper); left: 370px; top: 140px; font-size: 44px; }
</style>
</head>
<body>
<main class="stage">

  <section class="card card--front" aria-label="Business card front">
    <svg class="card__swoosh" viewBox="0 0 700 400" preserveAspectRatio="none" aria-hidden="true">
      <path d="M0 135 Q170 360 700 400 L0 400 Z" fill="var(--brand-red)"/>
      <path d="M45 200 Q240 355 640 392" fill="none" stroke="var(--gold)" stroke-width="5"/>
    </svg>

    <p class="company-name">EMBER<br>REALTY INC</p>

    <div class="divider"></div>

    <div class="contact">
      <p class="contact__name">DANIEL HARPER</p>
      <p class="contact__role">Founder and President</p>
      <p>1870 Maple Crest Drive</p>
      <p>Fairview, GA 30215</p>
      <ul class="contact__list">
        <li>
          <svg viewBox="0 0 12 12"><path d="M3 1 L5 3.5 L4 5 Q5.5 7 7 8 L8.5 7 L11 9 L9.5 11 Q4 10 1 2.5 Z" fill="var(--brand-red)"/></svg>
          +330 5172-4400
        </li>
        <li>
          <svg viewBox="0 0 12 12"><rect x="1" y="2.5" width="10" height="7" fill="none" stroke="var(--brand-red)" stroke-width="1.3"/><path d="M1 3 L6 7 L11 3" fill="none" stroke="var(--brand-red)" stroke-width="1.3"/></svg>
          info@emberrealtyinc.com
        </li>
        <li>
          <svg viewBox="0 0 12 12"><circle cx="6" cy="6" r="5" fill="none" stroke="var(--brand-red)" stroke-width="1.3"/><ellipse cx="6" cy="6" rx="2.2" ry="5" fill="none" stroke="var(--brand-red)" stroke-width="1"/><path d="M1 6 H11" stroke="var(--brand-red)" stroke-width="1"/></svg>
          www.emberrealtyinc.com
        </li>
      </ul>
    </div>
  </section>

  <section class="card card--back" aria-label="Business card back">
    <div class="portrait" role="img" aria-label="Portrait photo of the broker in a navy blazer and light blue shirt"></div>
    <p class="company-name company-name--light">EMBER<br>REALTY INC</p>
  </section>

</main>
</body>
</html>
```